Web Design Project for a Software & Consulting Company

We have just completed a recent ArtHerdly project for a new logo (see attached).
As the next stage of our rebranding we now require a website re-design to complement the new logo.
Our current site, http://www.corvinsoft.example was built in-house and does not come across as professional as we would like. We supply software and associated services to some of the world’s largest oil companies and we need our site to reflect that level of client.
We will also be posting another design project for brochures, PowerPoint slides and other materials very soon.
We would like designs for…
Home page
Product page
• TZQ
• BLV
• PNJ
Services
News page
About Us page
Contact Us page
Page for mobile devices that gives basic company and product information
Currently the site is small but we intend to increase content to include white papers etc. this should be taken into account when designing the navigation therefore we would prefer navigation through styled text links rather than images.
Colour schemes should broadly be taken from our new logo, where the dark blue and dark green from the left and right sides of the logo are the main colours, but other, brighter accent colours can be used to highlight sections or content.
Dark Blue = C:88, M:55, Y:44, K:28
Dark Green = C:87, M:53, Y:50, K:50
NB: Don’t use the logo on our current site, make sure you use the one attached.
We would prefer the final file format to be a layered PSD.
The site should be clean and professional and communicate the following...
• That we have a great depth and breadth of knowledge about our customers’ business, enabling us to deliver the best systems and solutions.
• That we are a leading provider of cost estimation and control solutions to the oil and gas industry.
• The benefits of our software and consulting services.
• Show that we deliver outstanding customer service and value with a very high level of professionalism
• The site should have no Flash and be able to self-adjust to fit any screen size.
Things to avoid …
• Obvious and clichéd oil industry imagery, no oil rigs
• Cartoon style graphics
Our Background
We are an integrated software and consulting organization specialising in the drilling side of the oil and gas industry. Simply put our software helps companies better understand, predict and communicate the cost of drilling wells.
We have 3 software products and a consulting offering consisting of…
• TZQ - Probabilistic time and cost software
• BLV – Cost tracking and reporting software
• PNJ – (currently known as DrillSavant) – Lessons learned software
• Consulting services
Our systems are in use in over 30 countries with a broad range of clients including: GN, Marovel, Dunt, Koruna, VELO Sirkami, FALUMI and Quintex.
Our current site can be found at www.corvinsoft.example
Our main competitors are
• http://www.drovanic.example/
• http://www.sumbrask.example/
• http://www.kve.example/services/software-solutions/p1-
Our depth of drilling knowledge, quality of software and collaboration with clients differentiate us form the competition.
We strive for very high levels of customer service.
We look forward to receiving your designs!
Updates
Thanks to all the designers who have submitted a design, we appreciate the effort.
We will do our best to give individual feedback on each design but given that many are quite similar we thought we would give some general feedback first.
Nearly all the designs submitted so far have been slight variations on…
-
Top Menu
-
Scrolling Photo Banner
-
4 Columns
-
Body
-
Deep Footer
These designs are well executed but they are basically the same layout as our existing site and while there is nothing inherently wrong with this layout we would like to see some designs that are a bit more innovative and different. We don’t really want just a polished version of our current site.
Thanks again,
CVS
Thanks to everyone who has submitted a design, the response has been great.
We are close to making a decision so if you are intending to submit a design please do it soon, the deadline is only a few days away.
Thanks again.
CVS
Target Market(s)
Mid to high level executives
Industry/Entity Type
Oil And Gas
Look and feel

```html
<!DOCTYPE html>
<html lang="en">
<head>
<meta charset="utf-8">
<title>Corvin Soft — Home</title>
<link href="https://fonts.googleapis.com/css2?family=Rambla:wght@400;700&family=Ubuntu:wght@400;500&display=swap" rel="stylesheet">
<style>
:root{
  --teal-dark:#1b4a58;
  --green-dark:#4d6a47;
  --heading:#1d4e5c;
  --box:#6aaeb4;
  --footer:#1d4653;
  --footer-line:#3e6571;
  --body-text:#333;
  --page-bg:#ececec;
}
*{margin:0;padding:0;box-sizing:border-box}
html,body{width:934px;height:1200px;overflow:hidden}
body{background:var(--page-bg);font-family:"Ubuntu",sans-serif;color:var(--body-text);position:relative}
.page{position:absolute;left:86px;top:0;width:763px;height:1200px;background:#fff;box-shadow:0 0 4px rgba(0,0,0,.25)}
.abs{position:absolute}
/* header */
.brand{left:8px;top:12px;display:flex;align-items:center;gap:6px}
.brand-mark{width:26px;height:26px;border-radius:50%;background:var(--teal-dark)}
.brand-name{font-family:"Rambla",sans-serif;font-weight:700;font-size:20px;color:var(--teal-dark);line-height:1}
.brand-sub{font-family:"Rambla",sans-serif;font-size:10px;letter-spacing:3px;color:var(--teal-dark)}
.nav{left:220px;top:33px;width:543px;height:40px;background:var(--teal-dark);display:flex}
.nav a{color:#fff;text-decoration:none;font-size:10px;padding:0 13px;line-height:40px;border-right:1px solid #2e5e6c}
.nav a.active{background:var(--green-dark);width:58px;text-align:center;padding:0}
.social{position:absolute;right:14px;top:11px;display:flex;gap:6px}
.social span{width:19px;height:19px;border-radius:50%;background:#fff}
.header-rule{left:0;top:99px;width:763px;height:2px;background:#d5dfe1}
.tagline{left:0;top:116px;width:763px;text-align:center;font-family:"Rambla",sans-serif;font-weight:700;color:var(--green-dark)}
.tagline .l1{font-size:15px}
.tagline .l2{font-size:17.5px;color:var(--green-dark)}
.tagline .l2 b{color:var(--teal-dark)}
.hero{left:8px;top:170px;width:748px;height:240px;background:linear-gradient(100deg,#c9ccd0 0%,#e8e6e3 35%,#c9a690 52%,#9aa2ad 70%,#5e6470 100%)}
.dots{left:373px;top:396px;display:flex;gap:3px}
.dots span{width:9px;height:9px;border-radius:50%;background:#fff}
.dots span:first-child{background:var(--teal-dark)}
/* left column */
.h2{font-family:"Rambla",sans-serif;font-weight:700;font-size:14px;color:var(--heading);border-bottom:1px solid var(--teal-dark);padding-bottom:2px}
.about-h{left:8px;top:424px;width:418px}
.about-p{left:8px;top:455px;width:418px;font-size:8.6px;line-height:15.7px}
.more{left:8px;top:510px;width:40px;height:17px;background:var(--teal-dark);color:#fff;font-size:8.5px;text-align:center;line-height:17px;border-radius:2px}
.benefits-h{left:8px;top:557px;width:418px}
.benefits{left:22px;top:593px;list-style:none}
.benefits li{height:23.4px;font-size:8.6px;display:flex;align-items:center;gap:14px}
.benefits li i{width:15px;height:15px;border-radius:50%;background:var(--green-dark);display:flex;align-items:center;justify-content:center}
.clients-h{left:14px;top:801px;width:412px}
.client{font-family:"Rambla",sans-serif;font-weight:700;font-size:17px;color:var(--teal-dark);display:flex;align-items:center;gap:5px}
.client span.dot{width:10px;height:10px;border-radius:50%;background:var(--green-dark)}
/* right column */
.card{left:466px;width:291px;height:90px;background:var(--box);color:#fff;display:flex;align-items:flex-start;padding:14px 14px 0 12px;gap:12px}
.card svg{flex:none;margin-top:8px}
.card h3{font-family:"Rambla",sans-serif;font-weight:700;font-size:12px;color:var(--teal-dark);margin-bottom:2px}
.card p{font-size:8.3px;line-height:13.8px}
.badge{left:466px;top:842px;width:291px;height:90px;background:linear-gradient(#3b8aa3,#1b4a58 55%,#173f4b);box-shadow:0 2px 3px rgba(0,0,0,.35)}
/* footer */
.footer{left:0;top:954px;width:763px;height:201px;background:var(--footer);color:#fff}
.f-col h4{font-weight:400;font-size:11.5px;margin-bottom:5px}
.f-col ul{list-style:none;border-top:1px solid var(--footer-line)}
.f-col li{font-size:9.5px;height:23px;line-height:23px;padding-left:7px;border-bottom:1px solid var(--footer-line)}
.f-divider{left:514px;top:30px;width:3px;height:160px;background:linear-gradient(90deg,rgba(0,0,0,.35),transparent)}
.phone{font-size:16px;color:#8e9e64}
.news-field{width:180px;height:24px;background:#fff;border-radius:2px;display:flex;overflow:hidden}
.news-field span{flex:1;font-size:8.5px;color:#222;line-height:24px;padding-left:7px}
.news-field b{width:42px;background:#dcdcdc;font-size:8px;font-weight:500;color:#333;text-align:center;line-height:24px}
.legal{left:0;top:1155px;width:763px;height:45px;background:#000;color:#fff;text-align:center;font-size:8px;line-height:12.5px;padding-top:11px}
</style>
</head>
<body>
<div class="page">
  <div class="abs brand">
    <span class="brand-mark"></span>
    <div><div class="brand-name">CORVIN SOFT</div><div class="brand-sub">TECHNOLOGIES</div></div>
  </div>
  <nav class="abs nav">
    <a class="active">HOME</a><a>PRODUCTS</a><a>SERVICES</a><a>NEWS</a><a>ABOUT US</a><a>CONTACT US</a>
    <div class="social"><span></span><span></span><span></span></div>
  </nav>
  <div class="abs header-rule"></div>
  <div class="abs tagline">
    <div class="l1">We are a leading provider of</div>
    <div class="l2"><b>Cost Estimation</b> and <b>Control Solutions</b> to the <b>Oil and Gas industry.</b></div>
  </div>
  <div class="abs hero" role="img" aria-label="Photo of two business people shaking hands"></div>
  <div class="abs dots"><span></span><span></span><span></span><span></span><span></span></div>

  <h2 class="abs h2 about-h">Some Words About Us</h2>
  <p class="abs about-p">Corvin Soft have developed and continue to support software in over 30 countries, providing real results to hundreds of drilling operations. With decades of hands-on software and well engineering experience, we are uniquely positioned to provide the right solution to our customers.</p>
  <div class="abs more">More</div>

  <h2 class="abs h2 benefits-h">The Benefits of our Software and Consulting Services</h2>
  <ul class="abs benefits">
    <li><i><svg width="8" height="8" viewBox="0 0 8 8"><path d="M1 1l3 3-3 3M4 1l3 3-3 3" stroke="#fff" stroke-width="1.3" fill="none"/></svg></i>Sed ut perspiciatis unde omnis iste natus error sit voluptatem</li>
    <li><i><svg width="8" height="8" viewBox="0 0 8 8"><path d="M1 1l3 3-3 3M4 1l3 3-3 3" stroke="#fff" stroke-width="1.3" fill="none"/></svg></i>Accusantium doloremque laudantium totam rem aperiam eaque</li>
    <li><i><svg width="8" height="8" viewBox="0 0 8 8"><path d="M1 1l3 3-3 3M4 1l3 3-3 3" stroke="#fff" stroke-width="1.3" fill="none"/></svg></i>Quae ab illo inventore veritatis et quasi architecto beatae vitae dicta Sunt</li>
    <li><i><svg width="8" height="8" viewBox="0 0 8 8"><path d="M1 1l3 3-3 3M4 1l3 3-3 3" stroke="#fff" stroke-width="1.3" fill="none"/></svg></i>explicabo. Nemo enim ipsam voluptatem quia voluptas sit</li>
    <li><i><svg width="8" height="8" viewBox="0 0 8 8"><path d="M1 1l3 3-3 3M4 1l3 3-3 3" stroke="#fff" stroke-width="1.3" fill="none"/></svg></i>Aspernatur aut odit aut fugit, sed quia consequuntur magni dolores</li>
    <li><i><svg width="8" height="8" viewBox="0 0 8 8"><path d="M1 1l3 3-3 3M4 1l3 3-3 3" stroke="#fff" stroke-width="1.3" fill="none"/></svg></i>Ratione voluptatem sequi nesciunt neque porro quisquam est</li>
    <li><i><svg width="8" height="8" viewBox="0 0 8 8"><path d="M1 1l3 3-3 3M4 1l3 3-3 3" stroke="#fff" stroke-width="1.3" fill="none"/></svg></i>Dolorem ipsum quia dolor sit amet, consectetur adipisci velit</li>
    <li><i><svg width="8" height="8" viewBox="0 0 8 8"><path d="M1 1l3 3-3 3M4 1l3 3-3 3" stroke="#fff" stroke-width="1.3" fill="none"/></svg></i>Numquam eius modi tempora incidunt ut labore et dolore</li>
  </ul>

  <h2 class="abs h2 clients-h">Our Clients</h2>
  <div class="abs client" style="left:20px;top:843px">Dunt</div>
  <div class="abs client" style="left:120px;top:843px">Koruna</div>
  <div class="abs client" style="left:268px;top:843px"><span class="dot"></span>GN</div>
  <div class="abs client" style="left:370px;top:843px">Marovel</div>
  <div class="abs client" style="left:20px;top:903px">Tarnel</div>
  <div class="abs client" style="left:120px;top:903px">FALUMI</div>
  <div class="abs client" style="left:268px;top:903px">VELO</div>
  <div class="abs client" style="left:370px;top:903px"><span class="dot"></span>Hadrix</div>

  <div class="abs card" style="top:432px">
    <svg width="48" height="48" viewBox="0 0 48 48"><circle cx="24" cy="24" r="21" stroke="#fff" stroke-width="3" fill="none"/><path d="M24 10v14l9 6" stroke="#fff" stroke-width="2.5" fill="none"/></svg>
    <div><h3>Time &amp; Cost Estimation</h3><p>TZQ delivers a standardized, systematic approach to understanding, quantifying and communicating the impact of project risk to all stakeholders. »</p></div>
  </div>
  <div class="abs card" style="top:526px">
    <svg width="48" height="48" viewBox="0 0 48 48"><g fill="none" stroke="#fff" stroke-width="3"><ellipse cx="24" cy="10" rx="15" ry="5"/><path d="M9 10v28c0 3 7 5 15 5s15-2 15-5V10M9 19c0 3 7 5 15 5s15-2 15-5M9 28c0 3 7 5 15 5s15-2 15-5"/></g></svg>
    <div><h3>Material &amp; Cost Control</h3><p>Since 1992 BLV has been helping companies optimize their materials and logistics processes and accurately track costs on a daily basis. »</p></div>
  </div>
  <div class="abs card" style="top:622px">
    <svg width="48" height="48" viewBox="0 0 48 48"><g fill="none" stroke="#fff" stroke-width="6"><path d="M40 20A17 17 0 0 0 9 17"/><path d="M8 28a17 17 0 0 0 31 3"/></g><path d="M34 14l10 0-4 10z" fill="#fff"/><path d="M14 34l-10 0 4-10z" fill="#fff"/></svg>
    <div><h3>Lesson Learned</h3><p style="line-height:11.3px">DrillSavant is an advanced lessons learned and knowledge management system for use in the Oil &amp; Gas industry. It's fully searchable and easy to use. »</p></div>
  </div>
  <div class="abs card" style="top:717px">
    <svg width="48" height="48" viewBox="0 0 48 48"><circle cx="18" cy="30" r="11" fill="none" stroke="#fff" stroke-width="6" stroke-dasharray="4 3"/><circle cx="18" cy="30" r="7" fill="#fff"/><circle cx="38" cy="12" r="6" fill="#fff"/></svg>
    <div><h3>Services &amp; Consulting</h3><p>Software solutions rely on people and processes to deliver results. From analysis through execution we support our clients to improve performance. »</p></div>
  </div>
  <div class="abs badge" role="img" aria-label="Software partner badge"></div>

  <footer class="abs footer">
    <div class="abs f-col" style="left:24px;top:38px;width:172px">
      <h4>Europe</h4>
      <ul><li>18 Harlow Crescent</li><li>Dunmere, DN4 2QT</li><li>Phone:+44(0)1632 960418</li><li>Email:&nbsp;&nbsp;&nbsp;eu@corvinsoft.example</li></ul>
    </div>
    <div class="abs f-col" style="left:272px;top:39px;width:164px">
      <h4>North America</h4>
      <ul><li>4100 Lakemont Pkwy, Suite 210</li><li>Brenford, TX 75099</li><li>Phone:(555) 014 2278</li><li>Email:&nbsp;&nbsp;&nbsp;us@corvinsoft.example</li></ul>
    </div>
    <div class="abs f-divider"></div>
    <div class="abs" style="left:542px;top:38px">
      <div style="font-size:11.5px">Questions?</div>
      <div class="phone" style="margin-top:3px">0800-555-01234</div>
      <div style="font-size:11.5px;margin:6px 0 0 3px">Follow Us</div>
      <div style="display:flex;gap:3px;margin:5px 0 0 3px"><span style="width:16px;height:16px;background:#3b5b99;border-radius:2px"></span><span style="width:16px;height:16px;background:#3a9fd6;border-radius:2px"></span><span style="width:16px;height:16px;background:#2d7fb5;border-radius:2px"></span><span style="width:16px;height:16px;background:#e46b26;border-radius:2px"></span></div>
      <div style="font-size:11.5px;margin:6px 0 0 1px">Newsletter:</div>
      <div class="news-field" style="margin:8px 0 0 1px"><span>Email address</span><b>SUBMIT</b></div>
    </div>
  </footer>
  <div class="abs legal">Copyright © 2013 Corvinsoft. All rights reserved<br>Privacy Policy | General conditions</div>
</div>
</body>
</html>
```